Brantor Works Business Card

Modern and Professional Business Card for a Med size construction/development company.

See the samples below for the design I like … but I need ideas for incorporating the red company logo while still keeping the clean look of the card samples that are attached.

Logo and tag line on the back … info on the front.

Tagline: Built Right from the Footing Up

Target Market(s)

Med-Large General Contractors

Contact Information for Business Card

Brantor Works Limited
42 Fenwick Avenue
Mt. Pearl, NL
A1N 4R9

t: 709-555-0147
f: 709-555-0182
w: www.brantorworks-example.com

Font styles to use
Sans Serif

Colors
fbee3e

Requirements
Must have
• I like the black and yellow designs of the attached samples …. but I'm not sure how to incorporate the red Brantor Works logo into that design??
Nice to have
• Construction safety strips

```html
<!DOCTYPE html>
<html lang="en">
<head>
<meta charset="utf-8">
<title>Brantor Works Business Card</title>
<link href="https://fonts.googleapis.com/css2?family=Lato:wght@400;700;900&display=swap" rel="stylesheet">
<style>
  :root {
    --stage: #2b2b2b;
    --card-yellow: #e3c51e;
    --card-black: #060708;
    --ink: #141414;
    --accent-red: #d9182a;
    --brand-yellow: #e0c11c;
    --rule: #8f7a12;
  }
  * { box-sizing: border-box; margin: 0; padding: 0; }
  html, body { width: 1200px; height: 917px; overflow: hidden; }
  body {
    background: var(--stage);
    font-family: "Lato", sans-serif;
    position: relative;
  }
  .card {
    position: absolute;
    width: 620px;
    height: 354px;
    box-shadow: 0 18px 40px rgba(0,0,0,.55);
  }
  /* Front */
  .card-front { left: 110px; top: 60px; background: var(--card-yellow); color: var(--ink); }
  .front-brand {
    position: absolute; left: 58px; top: 96px; width: 210px;
    font-weight: 900; font-size: 38px; line-height: 1.02;
    color: var(--accent-red); letter-spacing: .5px;
  }
  .front-divider { position: absolute; left: 300px; top: 70px; width: 1px; height: 126px; background: var(--rule); }
  .contact { position: absolute; left: 328px; top: 74px; }
  .contact-name { font-weight: 900; font-size: 27px; color: var(--ink); }
  .contact-title { font-size: 15px; color: var(--accent-red); margin-top: 2px; }
  .contact-list { list-style: none; margin-top: 12px; }
  .contact-list li {
    display: flex; align-items: center; gap: 10px;
    font-size: 15px; color: var(--accent-red); line-height: 24px;
  }
  .contact-list svg { width: 15px; height: 15px; fill: var(--ink); flex: none; }
  .front-footer { position: absolute; left: 0; right: 0; bottom: 58px; display: flex; align-items: center; justify-content: center; gap: 18px; }
  .footer-company { font-size: 15px; color: var(--ink); }
  .footer-divider { width: 1px; height: 42px; background: var(--rule); }
  .footer-address { font-size: 14px; color: var(--accent-red); line-height: 1.3; }
  /* Back */
  .card-back { left: 470px; top: 500px; background: var(--card-black); }
  .back-brand {
    position: absolute; left: 0; right: 0; top: 104px; text-align: center;
    font-weight: 900; font-size: 58px; line-height: 1; letter-spacing: 2px;
    color: var(--brand-yellow);
  }
  .back-sub {
    position: absolute; left: 0; right: 0; top: 176px; text-align: center;
    font-weight: 900; font-size: 26px; letter-spacing: 6px; color: var(--brand-yellow);
  }
  .tagline {
    position: absolute; left: 0; right: 0; bottom: 54px; text-align: center;
    font-size: 15px; letter-spacing: 1.5px; color: var(--brand-yellow);
  }
</style>
</head>
<body>
  <section class="card card-front" aria-label="Business card front">
    <div class="front-brand">BRANTOR WORKS</div>
    <div class="front-divider"></div>
    <div class="contact">
      <div class="contact-name">Marcus Hale</div>
      <div class="contact-title">Founder &amp; CEO</div>
      <ul class="contact-list">
        <li>
          <svg viewBox="0 0 16 16" aria-hidden="true"><path d="M1 5c2-3 12-3 14 0l-1 2-3-1V5H5v1L2 7zM4 8h8l2 6H2zm4 1.5a2 2 0 1 0 0 4 2 2 0 0 0 0-4z"/></svg>
          709-555-0147
        </li>
        <li>
          <svg viewBox="0 0 16 16" aria-hidden="true"><path d="M4 1h8v4H4zM1 6h14v6h-3v3H4v-3H1zm4 4v4h6v-4z"/></svg>
          709-555-0182
        </li>
        <li>
          <svg viewBox="0 0 16 16" aria-hidden="true"><path d="M8 1a7 7 0 1 0 0 14A7 7 0 0 0 8 1zm0 1.3c.9.8 1.6 2.2 1.8 4H6.2C6.4 4.5 7.1 3.1 8 2.3zM2.4 7.3h2.6v1.4H2.4zm8.6 0h2.6v1.4H11zM6.2 9.7h3.6c-.2 1.8-.9 3.2-1.8 4-.9-.8-1.6-2.2-1.8-4zM6.2 7.3h3.6v1.4H6.2z"/></svg>
          www.brantorworks-example.com
        </li>
      </ul>
    </div>
    <div class="front-footer">
      <span class="footer-company">Brantor Works Limited</span>
      <span class="footer-divider"></span>
      <span class="footer-address">42 Fenwick Avenue<br>Brookvale, NL B2K 3T8</span>
    </div>
  </section>

  <section class="card card-back" aria-label="Business card back">
    <div class="back-brand">BRANTOR WORKS</div>
    <div class="back-sub">LIMITED</div>
    <div class="tagline">BUILT RIGHT FROM THE FOOTING UP</div>
  </section>
</body>
</html>
```